Business Card Design

IT Solutions company.

I need a professional looking design with my company logo if possible.

Logo is located here:
http://www.brunelwavesystems.co.uk/dev/images/logo1.jpg
Feel free to redesign the logo if you think you have any better suggestions.

Our services include, IT Infrastructure/Telephony Maintenance & Hosting Services. Linux and Windows Solutions, App Development.

Out website is currently under development:
http://www.brunelwavesystems.co.uk/dev/

I'm looking for a colourful but professional looking business card.

Industry/Entity Type

Business

Contact Information for Business Card

BW Brunel Wavesystems Ltd
Martin Hollisby
07700958312
www.brunelwavesystems.co.uk
mhollisby@brunelwavesystems.co.uk

```html
<!DOCTYPE html>
<html lang="en">
<head>
<meta charset="utf-8">
<title>Brunel Wavesystems Ltd – Business Card</title>
<link rel="stylesheet" href="https://fonts.googleapis.com/css2?family=Bree+Serif&family=Open+Sans:wght@400;600&family=Arimo:wght@700&display=swap">
<style>
  :root{
    --backdrop:#3a2a22;
    --card-front:#ffffff;
    --card-back:#2b2d2d;
    --brand-blue:#1f4fe0;
    --ink:#262626;
    --rule:#c9ccd0;
    --back-text:#ffffff;
    --back-ghost:#363939;
  }
  *{box-sizing:border-box;margin:0;padding:0}
  html,body{width:1200px;height:483px;overflow:hidden}
  body{background:var(--backdrop);position:relative;font-family:"Open Sans",sans-serif}

  .card{position:absolute;top:76px;width:545px;height:331px;overflow:hidden;box-shadow:0 6px 18px rgba(0,0,0,.45)}
  .card--front{left:30px;background:var(--card-front)}
  .card--back{left:625px;background:var(--card-back);color:var(--back-text)}

  /* front */
  .brand{position:absolute;top:42px;left:0;right:0;text-align:center}
  .brand__name{font-family:"Open Sans",sans-serif;font-weight:600;font-size:28px;color:var(--ink);letter-spacing:.5px}

  .holder{position:absolute;top:150px;left:0;right:0;text-align:center}
  .holder__name{font-family:"Bree Serif",serif;font-weight:400;font-size:23px;color:var(--brand-blue)}
  .holder__rule{width:200px;height:1px;background:var(--rule);margin:6px auto 0}

  .contacts{position:absolute;top:204px;left:0;right:0;list-style:none}
  .contacts li{font-size:17px;color:var(--ink);line-height:25px;display:flex;align-items:center;justify-content:center;gap:8px}
  .contacts svg{width:14px;height:14px;fill:var(--ink);flex:none}

  .front-band{position:absolute;left:0;bottom:0;width:100%;height:70px}

  /* back */
  .ghost-name{position:absolute;top:128px;left:0;right:0;text-align:center;font-family:"Arimo",sans-serif;font-weight:700;font-size:40px;line-height:1;color:var(--back-ghost);white-space:nowrap}
  .services{position:absolute;top:58px;left:0;right:0;text-align:center;font-family:"Arimo",sans-serif;font-weight:700}
  .services__title{font-size:15px;font-weight:700}
  .services__rule{width:200px;height:1px;background:var(--back-text);margin:6px auto 10px}
  .services__list{list-style:none;font-size:15px;line-height:23px}
  .services__list li::before{content:"• "}
  .back-web{position:absolute;top:258px;left:0;right:0;text-align:center;font-family:"Arimo",sans-serif;font-weight:700;font-size:15px;letter-spacing:.5px}
</style>
</head>
<body>

<section class="card card--front" aria-label="Business card front">
  <div class="brand">
    <span class="brand__name">Brunel Wavesystems Ltd</span>
  </div>

  <div class="holder">
    <h1 class="holder__name">Martin Hollisby</h1>
    <div class="holder__rule"></div>
  </div>

  <ul class="contacts">
    <li>
      <svg viewBox="0 0 24 24" aria-hidden="true"><path d="M6.6 10.8a15.1 15.1 0 0 0 6.6 6.6l2.2-2.2a1 1 0 0 1 1-.25 11.4 11.4 0 0 0 3.6.57 1 1 0 0 1 1 1V20a1 1 0 0 1-1 1A17 17 0 0 1 3 4a1 1 0 0 1 1-1h3.5a1 1 0 0 1 1 1c0 1.25.2 2.45.57 3.6a1 1 0 0 1-.25 1z"/></svg>
      07700958312
    </li>
    <li>
      <svg viewBox="0 0 24 24" aria-hidden="true"><path d="M2 6h20v12H2z M2 6l10 7 10-7" stroke="#fff" stroke-width="1.5"/></svg>
      mhollisby@brunelwavesystems.co.uk
    </li>
    <li>
      <svg viewBox="0 0 24 24" aria-hidden="true"><circle cx="12" cy="12" r="10"/><path d="M2 12h20M12 2c3 3 3 17 0 20M12 2c-3 3-3 17 0 20" stroke="#fff" stroke-width="1.4" fill="none"/></svg>
      www.brunelwavesystems.co.uk
    </li>
  </ul>

  <svg class="front-band" viewBox="0 0 545 70" preserveAspectRatio="none" aria-hidden="true">
    <path d="M0 70 L0 58 Q20 46 60 44 L545 20 L545 70 Z" fill="var(--brand-blue)"/>
    <path d="M0 62 Q20 52 60 50 L545 27 L545 20 L60 44 Q20 46 0 58 Z" fill="#ffffff" opacity=".9"/>
  </svg>
</section>

<section class="card card--back" aria-label="Business card back">
  <div class="ghost-name" aria-hidden="true">Brunel Wavesystems</div>
  <div class="services">
    <h2 class="services__title">Our Services Include</h2>
    <div class="services__rule"></div>
    <ul class="services__list">
      <li>IT Infrastructure/Telephony Maintenance</li>
      <li>Hosting Services</li>
      <li>Linux and Windows Solutions</li>
      <li>App Development</li>
    </ul>
  </div>
  <p class="back-web">www.brunelwavesystems.co.uk</p>
</section>

</body>
</html>
```